Event flyer for Sunday night Youth Group

Need a 4 x 6 or 5 x 7 flyer for a new youth group starting on April 14. The youth group is for students in middle school and high school so it needs to look fun and cool, but not childish. I prefer it not to include pictures of people unless it's so obscure you can't really see their faces. I've uploaded some pictures of flyers I like. I've also attached a couple versions of our logo to use on the flyer.
Information the flyer needs to include:
Youth Group
Sundays, 6-8pm (beginning April 14)
Location: Marlowe's - 4219 Quarry Fern Ave N, Keizer, 97318
There will be dinner, games, friends, and a message.
Target Market(s)
Youth ages 13-18
Industry/Entity Type
Church
Font styles to use
Colors
Designer to choose colors to be used in the design.
Look and feel

```html
<!DOCTYPE html>
<html lang="en">
<head>
<meta charset="utf-8">
<title>Youth Group Sunday Flyer</title>
<link rel="stylesheet" href="https://fonts.googleapis.com/css2?family=Oswald:wght@600&family=Quicksand:wght@500;700&family=Yellowtail&display=block">
<style>
  :root {
    --page-bg: #d9d9e6;
    --flyer-black: #141210;
    --glow-olive: #8a8a2a;
    --glow-gold: #c9a332;
    --glow-amber: #9a5a1c;
    --glow-brown: #3a220e;
    --title-yellow: #f4e21a;
    --title-cream: #f8f3c2;
    --badge-red: #ec4a2e;
    --band-gold: #e8b23a;
    --ink-dark: #1a1208;
    --paper-white: #ffffff;
  }
  * { box-sizing: border-box; margin: 0; padding: 0; }
  html, body { width: 1200px; height: 900px; overflow: hidden; }
  body {
    background: var(--page-bg);
    font-family: "Quicksand", sans-serif;
    font-weight: 700;
    position: relative;
  }
  .flyer {
    position: absolute;
    left: 300px; top: 30px;
    width: 600px; height: 840px;
    background: var(--flyer-black);
    overflow: hidden;
    box-shadow: 0 18px 40px rgba(40, 40, 70, 0.35);
  }
  .crowd-art {
    position: absolute; inset: 110px 0 0 0;
    background:
      radial-gradient(circle at 30% 45%, rgba(230, 220, 120, 0.35) 0 60px, transparent 110px),
      radial-gradient(circle at 70% 38%, rgba(240, 230, 140, 0.3) 0 80px, transparent 150px),
      radial-gradient(circle at 45% 62%, rgba(255, 250, 200, 0.35) 0 40px, transparent 120px),
      linear-gradient(180deg, var(--flyer-black) 0%, #3b3612 22%, var(--glow-olive) 45%, var(--glow-gold) 62%, var(--glow-amber) 80%, var(--glow-brown) 100%);
  }
  .brand {
    position: absolute; top: 62px; right: 40px;
    display: flex; align-items: center; gap: 8px;
    color: var(--paper-white);
    font-size: 16px; font-weight: 700; letter-spacing: 1px; text-transform: uppercase;
  }
  .brand-mark { width: 12px; height: 12px; background: var(--paper-white); }
  .title-block { margin: 0; font-weight: 400; }
  .title {
    position: absolute;
    font-family: "Yellowtail", cursive;
    font-weight: 400;
    white-space: nowrap;
    background: linear-gradient(180deg, var(--title-cream) 0%, var(--title-yellow) 55%, #e2c410 100%);
    -webkit-background-clip: text; background-clip: text;
    color: transparent;
    filter: drop-shadow(3px 3px 0 #000);
    line-height: 1.1;
  }
  .title-youth { left: 50px; top: 140px; font-size: 190px; }
  .title-group { right: 40px; top: 320px; font-size: 160px; }
  .day-badge {
    position: absolute; left: 290px; top: 520px;
    padding: 2px 12px;
    background: var(--badge-red);
    border-radius: 4px;
    color: var(--paper-white);
    font-family: "Oswald", sans-serif; font-weight: 600; font-size: 36px; letter-spacing: 1px;
  }
  .when {
    position: absolute; left: 40px; top: 615px;
    color: var(--paper-white);
  }
  .icon { display: block; }
  .date { display: flex; align-items: flex-start; margin-top: 8px; }
  .date-day { font-size: 30px; line-height: 1; }
  .date-suffix { font-size: 16px; }
  .date-month { font-size: 18px; align-self: flex-end; }
  .time {
    display: inline-block; margin-top: 6px; padding: 2px 10px;
    background: var(--paper-white); color: var(--ink-dark);
    font-size: 20px; border-radius: 2px;
  }
  .where {
    position: absolute; left: 340px; top: 590px;
    color: var(--paper-white);
  }
  .address { margin-top: 12px; font-size: 21px; line-height: 1.35; }
  .info-band {
    position: absolute; left: 0; right: 0; bottom: 34px;
    padding: 7px 0;
    background: var(--band-gold);
    color: var(--ink-dark);
    text-align: center; font-size: 18px; font-weight: 700;
  }
</style>
</head>
<body>
  <main class="flyer">
    <div class="crowd-art" role="img" aria-label="Crowd silhouettes with raised hands under warm golden bokeh concert lights"></div>

    <div class="brand"><span class="brand-mark"></span><span class="brand-name">Harborline Fellowship</span></div>

    <h1 class="title-block">
      <span class="title title-youth">Youth</span>
      <span class="title title-group">Group</span>
    </h1>
    <div class="day-badge">SUNDAY</div>

    <section class="when">
      <svg class="icon" width="62" height="58" viewBox="0 0 62 58" fill="none" stroke="#fff" stroke-width="2.5" aria-hidden="true">
        <rect x="3" y="8" width="46" height="42" rx="3"/>
        <line x1="3" y1="18" x2="49" y2="18"/>
        <line x1="14" y1="3" x2="14" y2="12"/><line x1="26" y1="3" x2="26" y2="12"/><line x1="38" y1="3" x2="38" y2="12"/>
        <rect x="10" y="24" width="6" height="5"/><rect x="20" y="24" width="6" height="5"/><rect x="30" y="24" width="6" height="5"/>
        <rect x="10" y="34" width="6" height="5"/><rect x="20" y="34" width="6" height="5"/>
        <circle cx="48" cy="44" r="10" fill="#2a200c"/>
        <polyline points="48,38 48,44 53,46"/>
      </svg>
      <div class="date"><span class="date-day">14</span><span class="date-suffix">th</span><span class="date-month">APRIL</span></div>
      <span class="time">6-8pm</span>
    </section>

    <section class="where">
      <svg class="icon" width="70" height="64" viewBox="0 0 70 64" fill="none" stroke="#fff" stroke-width="2.5" aria-hidden="true">
        <polygon points="3,14 22,8 42,14 60,8 60,56 42,62 22,56 3,62"/>
        <polyline points="3,40 22,26 42,50"/>
        <path d="M50 30 C40 20 42 4 52 4 C62 4 64 20 54 30 L52 34 Z" fill="#4a3a12"/>
        <circle cx="52" cy="14" r="4"/>
      </svg>
      <p class="address">Marlowe's - 4219<br>Quarry Fern Ave N<br>Keizer, 97318</p>
    </section>

    <p class="info-band">There will be Dinner, Games, Friends, &amp; a Message</p>
  </main>
</body>
</html>
```